Book Cover: Quiet Harbor: Small Ceremonies For The Restless Soul

I would like a full cover spread- front, back and spine as well as a stand alone front cover for Kindle for the book. Design a cover that mirrors the profound depth and dynamic energy of 'Quiet Harbor.' Envision a visual tapestry that draws readers into a transformative journey, where spirituality and self-care unite. Explore vibrant colors, intricate textures, and a sense of inner radiance that beckons readers to explore the book's rich wisdom within. See images for design inspiration attached. Even though some of the images are cartoon, I'd like the cover to be more serious than playful and very elegant.

About this book (back cover copy)
Are you ready to embark on a transformative journey and elevate your daily existence? "Quiet Harbor" is a treasure trove of practical yet profound rituals and wisdom from renowned self-care, healing, and spirituality experts.

Within these pages, you'll uncover a tapestry of guidance and insight from some of the world's most respected mentors. Their collective wisdom is your key to creating a sacred sanctuary within your everyday life.

From invigorating morning rituals to meditative practices, empowering affirmations, and transformative energy healing, you'll find a rich tapestry of tools to nurture a deeper connection with yourself and the universe.

Whether you're a seasoned practitioner or a newcomer to the world of self-care and spirituality, "Quiet Harbor" is your trusted companion on the journey to transform your life and elevate your daily experience. Open this book today and start your sacred, fulfilling adventure.

Colors
0094D4
00A9DD
6FCCEA
C7EBF8
E9F6FB
E54698
E96AAD
F1A4CE
F9D9EA
FCEFF6
6B429C
8869AF
B7A5CE
E3DAEB
F3F0F8

Requirements
Must have
• Title: Quiet Harbor: Subtitle: Small Ceremonies For The Restless Soul Name of Publisher: Lantern Bough Publishing- Logo on the back Back cover copy

```html
<!DOCTYPE html>
<html lang="en">
<head>
<meta charset="utf-8">
<title>Quiet Harbor – Cover Spread</title>
<link href="https://fonts.googleapis.com/css2?family=Great+Vibes&family=Crimson+Pro:ital,wght@0,400;0,600;0,700;1,400&family=Arimo:wght@400;700&display=swap" rel="stylesheet">
<style>
  :root {
    --stage: #2b2b2b;
    --paper: #fdfdfc;
    --ink: #1d1d1d;
    --subtitle-grey: #7d7d7d;
    --teal-deep: #2f6f6e;
    --teal-mid: #5f9e9a;
    --sage-pale: #cfe2df;
    --blush: #f6c6d3;
    --blush-pale: #fbe4ea;
    --gold-light: #f3d77a;
    --gold-mid: #d4a93c;
    --gold-deep: #a67c23;
    --spine-publisher: #2d6a74;
  }
  * { box-sizing: border-box; margin: 0; padding: 0; }
  html, body { width: 1200px; height: 1200px; overflow: hidden; }
  body { background: var(--stage); position: relative; }

  .spread {
    position: absolute; left: 20px; top: 189px;
    width: 1160px; height: 822px;
    display: flex; background: var(--paper);
  }
  .panel { position: relative; height: 100%; overflow: hidden; background: var(--paper); }
  .back-cover { width: 536px; }
  .spine { width: 58px; }
  .front-cover { width: 566px; }

  .botanical { position: absolute; border-radius: 50%; filter: blur(6px); }

  .gold-script {
    font-family: "Great Vibes", cursive;
    background: linear-gradient(100deg, var(--gold-deep) 0%, var(--gold-light) 35%, var(--gold-mid) 60%, var(--gold-deep) 100%);
    -webkit-background-clip: text; background-clip: text; color: transparent;
    line-height: 1; white-space: nowrap;
  }

  /* back cover */
  .back-title { position: absolute; left: 0; right: 0; top: 66px; text-align: center; }
  .back-title .word-one { font-size: 84px; display: block; }
  .back-title .word-two { font-size: 62px; display: block; margin: -22px 0 0 40px; }
  .back-subtitle {
    position: absolute; left: 0; right: 0; top: 196px; text-align: center;
    font-family: "Crimson Pro", serif; font-size: 24px; color: var(--subtitle-grey);
  }
  .back-subtitle em { font-style: italic; }
  .blurb {
    position: absolute; left: 62px; width: 412px; top: 236px; text-align: center;
    font-family: "Crimson Pro", serif; font-size: 14.5px; line-height: 1.31; color: var(--ink);
  }
  .blurb p + p { margin-top: 15px; }
  .blurb strong { font-weight: 700; }
  .publisher-mark {
    position: absolute; left: 150px; top: 714px; width: 210px; text-align: center;
    font-family: "Crimson Pro", serif; font-size: 21px; color: var(--ink); line-height: 1.25;
  }

  /* spine */
  .spine-text {
    position: absolute; left: 50%; top: 30px; transform: translateX(-50%);
    writing-mode: vertical-rl; display: flex; align-items: center; gap: 12px; white-space: nowrap;
  }
  .spine-title { font-size: 46px; }
  .spine-subtitle { font-family: "Crimson Pro", serif; font-size: 19px; color: var(--subtitle-grey); }
  .spine-subtitle em { font-style: italic; }
  .spine-publisher { font-family: "Arimo", sans-serif; font-size: 17px; color: var(--spine-publisher); margin-top: 10px; }
  .spine-publisher b { font-weight: 700; }

  /* front cover */
  .front-title { position: absolute; left: 20px; top: 360px; }
  .front-title .word-one { font-size: 178px; display: block; }
  .front-title .word-two { font-size: 130px; display: block; margin: -60px 0 0 120px; }
  .front-subtitle {
    position: absolute; left: 60px; width: 330px; top: 666px; text-align: center;
    font-family: "Crimson Pro", serif; font-size: 28px; line-height: 1.15; color: var(--subtitle-grey);
  }
  .front-subtitle em { font-style: italic; }
  .front-subtitle .strong-line { font-weight: 600; }
</style>
</head>
<body>
  <main class="spread">
    <section class="panel back-cover">
      <div class="botanical" role="img" aria-label="Pale pink watercolour blossom at the top left" style="left:-40px;top:20px;width:180px;height:180px;background:radial-gradient(circle,var(--blush-pale),transparent 70%);"></div>
      <div class="botanical" role="img" aria-label="Soft sage watercolour leaves along the top edge" style="left:120px;top:-50px;width:340px;height:120px;background:radial-gradient(ellipse,var(--sage-pale),transparent 70%);"></div>
      <div class="botanical" role="img" aria-label="Teal and sage watercolour leaves in the lower left corner" style="left:-70px;top:440px;width:300px;height:420px;background:radial-gradient(ellipse at 35% 65%,var(--teal-mid) 0%,var(--sage-pale) 50%,transparent 75%);"></div>

      <h2 class="back-title gold-script"><span class="word-one">Quiet</span><span class="word-two">Harbor</span></h2>
      <p class="back-subtitle"><em>Small Ceremonies for</em> The Restless Soul</p>
      <div class="blurb">
        <p><strong>Are you ready to embark on a transformative journey and elevate your daily existence?</strong> <em>"Quiet Harbor"</em> is a treasure trove of practical yet profound rituals and wisdom from renowned self-care, healing, and spirituality experts.</p>
        <p>Within these pages, you'll uncover a tapestry of guidance and insight from some of the world's most respected mentors. Their collective wisdom is your key to creating a sacred sanctuary within your everyday life.</p>
        <p>From invigorating morning rituals to meditative practices, empowering affirmations, and transformative energy healing, you'll find a rich tapestry of tools to nurture a deeper connection with yourself and the universe.</p>
        <p>Whether you're a seasoned practitioner or a newcomer to the world of self-care and spirituality, "Quiet Harbor" is your trusted companion on the journey to transform your life and elevate your daily experience. Open this book today and start your sacred, fulfilling adventure.</p>
      </div>
      <p class="publisher-mark">Lantern Bough<br>Publishing</p>
    </section>

    <section class="panel spine">
      <div class="botanical" role="img" aria-label="Faint sage leaves fading across the spine" style="left:-30px;top:60px;width:110px;height:200px;background:radial-gradient(ellipse,var(--sage-pale),transparent 70%);"></div>
      <div class="spine-text">
        <span class="spine-title gold-script">Quiet Harbor</span>
        <span class="spine-subtitle"><em>Small Ceremonies for</em> The Restless Soul</span>
        <span class="spine-publisher"><b>Lantern Bough</b> Publishing</span>
      </div>
    </section>

    <section class="panel front-cover">
      <div class="botanical" role="img" aria-label="Watercolour teal leaves and pink blossoms sweeping down the top right corner" style="left:110px;top:-80px;width:520px;height:440px;background:radial-gradient(ellipse at 70% 35%,var(--blush) 0%,var(--teal-deep) 30%,var(--teal-mid) 50%,var(--sage-pale) 65%,transparent 78%);"></div>
      <div class="botanical" role="img" aria-label="Soft sage leaves at the top left" style="left:-60px;top:40px;width:260px;height:200px;background:radial-gradient(ellipse,var(--sage-pale),transparent 70%);"></div>
      <div class="botanical" role="img" aria-label="Pale eucalyptus sprigs in the lower right" style="left:340px;top:560px;width:260px;height:280px;background:radial-gradient(ellipse,var(--sage-pale),transparent 70%);"></div>
      <div class="botanical" role="img" aria-label="Faint pink blossom and sage leaves along the bottom edge" style="left:40px;top:720px;width:320px;height:160px;background:radial-gradient(ellipse,var(--blush-pale),transparent 70%);"></div>

      <h1 class="front-title gold-script"><span class="word-one">Quiet</span><span class="word-two">Harbor</span></h1>
      <p class="front-subtitle"><em>Small Ceremonies for</em><br><span class="strong-line">The Restless</span><br><span class="strong-line">Soul</span></p>
    </section>
  </main>
</body>
</html>
```